MBR - Stationery Design Project

We need stationery based on our logo.

Company info :
Cabinet Voisard & Associés
Société à responsabilité limitée au capital de 200.000 FCFP
RCS Papeete 27586K - Numéro tahiti K73962
Centre d’affaires OPALE - Rue Gaston Perrin
BP 61384 MAHU POTE - 98752 Papeete
Tahiti - Polynésie française
Tél : +689 40 73 16 48
Fax : +689 40 39 64 91

Industry/Entity Type

It Company

Font styles to use
Sans Serif

```html
<!DOCTYPE html>
<html lang="fr">
<head>
<meta charset="utf-8">
<title>MBR – Papier à en-tête</title>
<link rel="stylesheet" href="https://fonts.googleapis.com/css2?family=Questrial&display=swap">
<style>
  :root {
    --backdrop: #a3b4b4;
    --paper: #f5f5f5;
    --brand-navy: #1b2540;
    --watermark: #e3e3e3;
    --footer-ink: #5a5f66;
    --rule: #3a3f46;
  }
  html, body {
    margin: 0;
    padding: 0;
    width: 1200px;
    height: 1000px;
    overflow: hidden;
    background: var(--backdrop);
    font-family: "Questrial", "Century Gothic", sans-serif;
  }
  .letterhead {
    position: absolute;
    left: 362px;
    top: 167px;
    width: 452px;
    height: 646px;
    background: var(--paper);
    box-shadow: 0 2px 6px rgba(0,0,0,0.12);
  }
  .brand {
    position: absolute;
    left: 36px;
    top: 22px;
    color: var(--brand-navy);
  }
  .brand-name {
    font-size: 52px;
    line-height: 46px;
    letter-spacing: -1px;
  }
  .brand-company {
    font-size: 10.5px;
    line-height: 12px;
    margin-top: 2px;
  }
  .brand-tagline {
    font-size: 5px;
    line-height: 6px;
    margin-left: 18px;
  }
  .watermark {
    position: absolute;
    left: 78px;
    top: 250px;
    font-size: 160px;
    line-height: 140px;
    letter-spacing: -4px;
    color: var(--watermark);
  }
  .footer {
    position: absolute;
    left: 0;
    top: 597px;
    width: 235px;
  }
  .footer-rule {
    height: 1px;
    background: var(--rule);
    margin-bottom: 5px;
  }
  .footer-text {
    margin: 0 0 0 19px;
    font-size: 5px;
    line-height: 8.5px;
    color: var(--footer-ink);
    white-space: nowrap;
  }
</style>
</head>
<body>
  <main class="letterhead">
    <header class="brand">
      <div class="brand-name">MBR</div>
      <div class="brand-company">Cabinet Voisard &amp; Associés</div>
      <div class="brand-tagline">Expertise-comptable · Audit · Conseil</div>
    </header>

    <div class="watermark" aria-hidden="true">MBR</div>

    <footer class="footer">
      <div class="footer-rule"></div>
      <p class="footer-text">
        Cabinet Voisard &amp; Associés - Société à responsabilité limitée au capital de 200.000 FCFP<br>
        RCS Papeete 27586K - Numéro tahiti K73962<br>
        Centre d’affaires OPALE - Rue Gaston Perrin BP 61384 MAHU POTE - 98752 Papeete Tahiti - Polynésie française<br>
        Tél : +689 40 73 16 48 &nbsp;|&nbsp; Fax : +689 40 39 64 91
      </p>
    </footer>
  </main>
</body>
</html>
```